Website for Plumbing Company, Mr. FlowKettle

I need a 7-page fully HTML-coded website for my plumbing company, Mr. FlowKettle. We specialize in installation, repair, and replacement of both gas and electric water heaters. Although we offer both tankless (on-demand) water heaters and standard (with tank) water heaters, most of our business is related to standard (with tank) water heaters in the USA market.

These are the pages I need:
1. Home page with sections such as About Us, Our Services, Why Choose Us, Testimonials, Location Map (Palm Beach County Florida), Quote Request Form, Join Our Newsletter, Mission Statement, etc.

2. Gas Water Heaters

3. Electric Water Heaters

4. Tankless Water Heaters

5. About Us

6. Contact Us

7. Privacy Policy, Terms & Conditions

Be sure to mention the following points:
1. Same-Day Service
2. Best Price Guarantee
3. 100% Satisfaction Rating
4. 15-Year Warranty on Water Heater & Parts
5. Lifetime Warranty on Workmanship
*All Warranties are Transferrable Upon Home Sale

Once design is selected and finalized, I need the website coded in a standard HTML/CSS and temporarily hosted on your development server so I can see the website functionality that is not observable from screenshots, such as section animations, etc. Once those details are finalized, I will move the source code to my server and complete the project.

Residential Home Owners and Business Owners

Plumbing, Home Services, Remodeling, Construction

0054AA
0677BA
7BADD7
CADEEF
E8F1F8
FFC000
F8CF3A
FAE287
FDF2CF
FEFAEE
EE7325
F08F49
F5BC92
FAE3D3
FDF4ED

• Clean, colorful, and professional

```html
<!DOCTYPE html>
<html lang="en">
<head>
<meta charset="utf-8">
<title>Mr. FlowKettle — Water Heater Service in Palm Beach County</title>
<link rel="stylesheet" href="https://fonts.googleapis.com/css2?family=Montserrat:wght@500;600;700&family=Lato:ital,wght@0,400;0,700;1,400&display=swap">
<style>
:root{
  --red:#d8322a;
  --navy:#1c2a6d;
  --navy-deep:#19236a;
  --ink:#2b2b2b;
  --body:#3d3d3d;
  --muted:#777;
  --panel:#f1f1f1;
  --line:#dcdcdc;
  --white:#ffffff;
}
*{box-sizing:border-box;margin:0;padding:0}
html,body{width:1200px;height:4342px;overflow:hidden}
body{position:relative;background:var(--white);font-family:"Lato",sans-serif;color:var(--body)}
.abs{position:absolute}
.head-font{font-family:"Montserrat",sans-serif}
.topbar{left:0;top:0;width:1200px;height:7px;background:var(--red)}
.header{left:0;top:7px;width:1200px;height:84px;background:var(--white)}
.brand{font-family:"Lato",sans-serif;font-weight:700;color:var(--navy);font-size:21px;display:flex;align-items:center;gap:9px}
.brand .dot{width:26px;height:26px;border-radius:50%;background:var(--red)}
.nav{left:342px;top:38px;display:flex;gap:0;font-size:14.5px;color:var(--ink)}
.nav a{color:var(--ink);text-decoration:none;position:absolute;white-space:nowrap}
.nav a.active{color:var(--red);text-decoration:underline}
.hero{left:0;top:91px;width:1200px;height:656px;background:linear-gradient(90deg,#3f4850 0%,#707b84 30%,#9aa3a8 52%,#6b6a63 72%,#3c3c44 100%)}
.hero-title{left:108px;top:285px;font-family:"Montserrat",sans-serif;font-weight:700;font-size:51px;line-height:64px;color:var(--white);letter-spacing:.5px}
.hero-sub{left:108px;top:436px;font-size:16px;font-weight:700;color:var(--white)}
.btn{background:var(--navy);color:var(--white);font-weight:700;font-size:16px;border-radius:4px;display:flex;align-items:center;justify-content:center}
h2.sec{position:absolute;font-family:"Montserrat",sans-serif;font-weight:600;font-size:38px;color:var(--navy);white-space:nowrap}
h2.sec span{color:var(--red)}
.center{left:0;width:1200px;text-align:center}
.about-frame{left:108px;top:829px;width:450px;height:408px;border:2px solid var(--red);border-radius:12px}
.about-photo{left:125px;top:840px;width:433px;height:400px;border-radius:8px;background:linear-gradient(135deg,#5e5648,#8c8a80 45%,#d9dde0 70%,#b9c3c9)}
.about-text{left:640px;top:887px;width:449px;font-size:14px;line-height:25.8px;text-align:justify;color:var(--ink)}
.services{left:0;top:1326px;width:1200px;height:604px;background:var(--panel)}
.intro{font-size:14px;line-height:26px;color:var(--ink)}
.card{background:var(--white);border:1px solid var(--line);border-radius:9px;overflow:hidden;box-shadow:0 2px 5px rgba(0,0,0,.1)}
.card-img{width:100%;height:268px}
.card-label{height:44px;display:flex;align-items:center;justify-content:space-between;padding:0 18px 0 20px;font-weight:700;font-size:16px;color:var(--ink)}
.go{width:19px;height:19px;border-radius:50%;background:#4a4a4a;display:flex;align-items:center;justify-content:center}
.arrow-btn{width:28px;height:28px;border-radius:50%;border:1.5px solid #333;display:flex;align-items:center;justify-content:center;background:var(--white)}
.mission-lead{font-size:16px;font-weight:700;color:var(--ink)}
.mission-text{left:138px;top:2103px;width:924px;text-align:center;font-size:14px;line-height:29.5px;color:var(--ink)}
.badge{width:70px;height:70px;border-radius:50%;background:var(--navy-deep);display:flex;align-items:center;justify-content:center;border:3px solid #fff;box-shadow:0 0 0 1px var(--navy-deep)}
.perk{font-size:16px;font-weight:700;color:var(--ink);white-space:nowrap}
.contact-band{left:0;top:2774px;width:1200px;height:647px;background:var(--panel)}
.map{left:110px;top:2978px;width:448px;height:277px;border-radius:12px;background:linear-gradient(160deg,#cfe4ec,#a9d3e4 45%,#6fc0d8 80%,#8ad0df);border:2px solid #e8e8e8}
.info{font-size:14.5px;color:var(--ink);display:flex;align-items:center;gap:12px;white-space:nowrap}
.ico-red{width:21px;height:21px;border-radius:50%;background:var(--red);display:flex;align-items:center;justify-content:center}
.form-card{left:642px;top:2978px;width:448px;height:354px;background:var(--white);border-radius:12px;box-shadow:0 2px 10px rgba(0,0,0,.12)}
.field{position:absolute;left:30px;width:390px;height:48px;border:1px solid #d8d8d8;border-radius:6px;display:flex;align-items:center;gap:12px;padding:0 16px 0 24px;font-size:14px;color:#6b6b6b;box-shadow:0 1px 3px rgba(0,0,0,.08)}
.t-card{background:var(--white);border:1px solid var(--line);border-radius:8px;box-shadow:0 2px 6px rgba(0,0,0,.1);height:277px;width:310px}
.stars{position:absolute;left:22px;top:30px;display:flex;gap:2px}
.quote{position:absolute;left:22px;top:66px;width:270px;font-size:15px;line-height:25px;color:#4a4a4a}
.more{position:absolute;left:22px;top:142px;font-size:14.5px;font-style:italic;text-decoration:underline;color:#555}
.avatar{position:absolute;left:27px;top:178px;width:80px;height:80px;border-radius:50%}
.who{position:absolute;left:127px;top:190px}
.who b{display:block;font-family:"Montserrat",sans-serif;font-weight:600;font-size:19px;color:var(--ink)}
.who small{display:block;font-size:14px;color:#444;margin-top:6px}
.footer{left:0;top:3936px;width:1200px;height:406px;background:var(--navy-deep);color:var(--white)}
.f-title{font-size:16px;font-weight:400;color:var(--white)}
.f-list{list-style:none;font-size:14.5px;line-height:34px}
.f-list li{display:flex;align-items:center;gap:14px}
.f-list li::before{content:"";width:7px;height:7px;border-radius:50%;background:var(--white)}
.f-contact{font-size:14.5px;line-height:24px;display:flex;gap:12px;align-items:flex-start}
.ico-w{width:18px;height:18px;border-radius:50%;background:var(--white);flex:none;display:flex;align-items:center;justify-content:center;margin-top:3px}
.news{left:110px;top:4148px;width:239px;height:43px;border:1px solid #8d93b8;border-radius:4px;display:flex;align-items:center;padding-left:20px;font-size:13.5px;color:#e6e8f2}
.news-go{position:absolute;right:3px;top:3px;width:44px;height:35px;background:var(--white);border-radius:3px;display:flex;align-items:center;justify-content:center}
.social{width:22px;height:22px;border-radius:50%;background:var(--white)}
.rule{left:110px;top:4281px;width:980px;height:1px;background:#4a528a}
.legal{font-size:14px;color:var(--white)}
</style>
</head>
<body>

<div class="abs topbar"></div>
<header class="abs header">
  <div class="abs brand" style="left:110px;top:24px"><span class="dot"></span>Mr. FlowKettle</div>
  <nav class="abs nav" style="left:0;top:33px">
    <a class="active" style="left:342px">Home</a>
    <a style="left:406px">Gas Water Heaters</a>
    <a style="left:560px">Electric Water Heaters</a>
    <a style="left:742px">Tankless Water Heaters</a>
    <a style="left:925px">About Us</a>
    <a style="left:1011px">Contact Us</a>
  </nav>
</header>

<section class="abs hero" role="img" aria-label="Technician in a hard hat and plaid shirt checking a tablet beside industrial water heater equipment"></section>
<h1 class="abs hero-title">Fast Reliable Guaranteed<br>Water Heater Service</h1>
<p class="abs hero-sub">Same-Day Installation, Repair &amp; Replacement in Palm Beach County</p>
<div class="abs btn" style="left:111px;top:479px;width:214px;height:47px">Request a Free Quote</div>

<div class="abs about-frame"></div>
<div class="abs about-photo" role="img" aria-label="Technician adjusting a wall-mounted white water heater unit"></div>
<h2 class="sec" style="left:640px;top:818px;font-size:38px"><span>About</span> Mr. FlowKettle</h2>
<div class="abs about-text">
  <p style="text-align:left">Water Heaters Are All We Do — And We Do Them Right</p>
  <p>At Mr. FlowKettle, we’re not a “do-everything” plumbing company. We focus on one thing and do it exceptionally well: water heaters. Serving homeowners throughout Palm Beach County, Florida, we specialize in the installation, repair, and replacement of gas and electric water heaters, with deep expertise in standard tank systems—the most reliable and cost-effective solution for most U.S. homes. While we also offer tankless water heater installations, our day-to-day work is centered on delivering dependable, long-lasting tank water heater solutions.</p>
</div>
<div class="abs btn" style="left:640px;top:1193px;width:130px;height:49px">Read More</div>

<section class="abs services"></section>
<h2 class="sec center" style="top:1398px"><span>Our</span> Services</h2>
<p class="abs center intro" style="top:1457px">At Mr. FlowKettle, we specialize exclusively in water heaters. Whether your unit needs a quick repair or a full<br>replacement, our experienced technicians deliver fast, dependable service—often the same day.</p>
<div class="abs arrow-btn" style="left:40px;top:1673px"><svg width="14" height="14" viewBox="0 0 14 14"><path d="M12 7H2M6 3 2 7l4 4" fill="none" stroke="#333" stroke-width="1.6"/></svg></div>
<div class="abs arrow-btn" style="left:1133px;top:1673px"><svg width="14" height="14" viewBox="0 0 14 14"><path d="M2 7h10M8 3l4 4-4 4" fill="none" stroke="#333" stroke-width="1.6"/></svg></div>
<div class="abs card" style="left:110px;top:1530px;width:306px">
  <div class="card-img" role="img" aria-label="Tall silver tank water heater in a basement" style="background:linear-gradient(135deg,#2f3a40,#5f6d73 50%,#aeb5b8)"></div>
  <div class="card-label">Water Heater Installation<span class="go"><svg width="10" height="10" viewBox="0 0 10 10"><path d="M1 5h7M5 2l3 3-3 3" fill="none" stroke="#fff" stroke-width="1.6"/></svg></span></div>
</div>
<div class="abs card" style="left:447px;top:1530px;width:306px">
  <div class="card-img" role="img" aria-label="Technician in a cap repairing an open water heater unit" style="background:linear-gradient(135deg,#e9e6df,#c9b79e 45%,#8fa1ad)"></div>
  <div class="card-label">Water Heater Repair<span class="go"><svg width="10" height="10" viewBox="0 0 10 10"><path d="M1 5h7M5 2l3 3-3 3" fill="none" stroke="#fff" stroke-width="1.6"/></svg></span></div>
</div>
<div class="abs card" style="left:784px;top:1530px;width:306px">
  <div class="card-img" role="img" aria-label="Hands servicing the burner of a gas water heater" style="background:linear-gradient(135deg,#f0f0ee,#d6d3cc 45%,#c86a55)"></div>
  <div class="card-label">Gas Water Heater Services<span class="go"><svg width="10" height="10" viewBox="0 0 10 10"><path d="M1 5h7M5 2l3 3-3 3" fill="none" stroke="#fff" stroke-width="1.6"/></svg></span></div>
</div>

<h2 class="sec center" style="top:1998px"><span>Our</span> Mission</h2>
<p class="abs center mission-lead" style="top:2064px">Reliable Hot Water. Honest Service. Guaranteed Results.</p>
<p class="abs mission-text">At Mr. FlowKettle, our mission is to provide homeowners with dependable, affordable, and long-lasting water heater solutions—without stress, surprises, or shortcuts. We focus exclusively on water heaters so we can deliver faster service, better installations, and real peace of mind. Every job is completed with expert workmanship, transparent pricing, and respect for your home. We stand behind everything we do with industry-leading warranties, same-day service when you need it most, and a commitment to 100% customer satisfaction.</p>

<h2 class="sec center" style="top:2284px"><span>Why Choose</span> Mr. FlowKettle</h2>
<p class="abs center perk" style="top:2378px">15-Year Warranty on Water Heater &amp; Parts</p>
<svg class="abs" style="left:0;top:2380px" width="1200" height="320" viewBox="0 2380 1200 320">
  <path d="M376 2653 A222 222 0 0 1 817 2653" fill="none" stroke="#1c2a6d" stroke-width="3" stroke-dasharray="12 8"/>
</svg>
<div class="abs badge" style="left:562px;top:2421px"><svg width="36" height="36" viewBox="0 0 24 24"><path d="M12 2 4 5v6c0 5 3.5 9 8 11 4.5-2 8-6 8-11V5z" fill="none" stroke="#fff" stroke-width="1.6"/><path d="m8.5 12 2.5 2.5 4.5-5" fill="none" stroke="#fff" stroke-width="1.8"/></svg></div>
<div class="abs badge" style="left:408px;top:2498px"><svg width="34" height="34" viewBox="0 0 24 24"><circle cx="12" cy="12" r="9" fill="none" stroke="#fff" stroke-width="1.5"/><path d="M8 16v-5h2l2-4c1 0 1.5.8 1.2 2L13 11h3l-1 5z" fill="none" stroke="#fff" stroke-width="1.4"/></svg></div>
<div class="abs badge" style="left:718px;top:2503px"><svg width="34" height="34" viewBox="0 0 24 24"><circle cx="12" cy="10" r="7" fill="none" stroke="#fff" stroke-width="1.5"/><path d="M12 6v8M14.2 7.6c-.6-.6-3.9-.9-3.9.9 0 1.8 3.9 1 3.9 2.9 0 1.8-3.3 1.5-4 .8M8 16l-2 6 3-1 2 2 1-4M16 16l2 6-3-1-2 2-1-4" fill="none" stroke="#fff" stroke-width="1.3"/></svg></div>
<div class="abs badge" style="left:341px;top:2618px"><svg width="34" height="34" viewBox="0 0 24 24"><rect x="3" y="5" width="15" height="15" rx="1" fill="none" stroke="#fff" stroke-width="1.5"/><path d="M3 9h15M7 3v4M14 3v4" stroke="#fff" stroke-width="1.5"/><circle cx="17" cy="17" r="4.5" fill="#19236a" stroke="#fff" stroke-width="1.4"/><path d="M17 15v2l1.5 1" stroke="#fff" stroke-width="1.3" fill="none"/></svg></div>
<div class="abs badge" style="left:782px;top:2618px"><svg width="34" height="34" viewBox="0 0 24 24"><path d="M6 21v-7h3l3-6c1.5 0 2 1 1.6 2.5L13 13h5l-1.5 8z" fill="none" stroke="#fff" stroke-width="1.5"/><path d="m6 3 .8 1.6 1.7.2-1.2 1.2.3 1.7L6 6.9l-1.6.8.3-1.7-1.2-1.2 1.7-.2zM18 3l.8 1.6 1.7.2-1.2 1.2.3 1.7-1.6-.8-1.6.8.3-1.7-1.2-1.2 1.7-.2z" fill="#fff"/></svg></div>
<div class="abs brand" style="left:480px;top:2590px;width:245px;justify-content:center;font-size:24px"><span class="dot"></span>Mr. FlowKettle</div>
<p class="abs perk" style="left:108px;top:2518px">Lifetime Warranty on Workmanship</p>
<p class="abs perk" style="left:817px;top:2528px">Best Price Guarantee</p>
<p class="abs perk" style="left:192px;top:2643px">Same-Day Service</p>
<p class="abs perk" style="left:888px;top:2648px">100% Satisfaction Rating</p>

<section class="abs contact-band"></section>
<h2 class="sec center" style="top:2855px"><span>Get Your Hot</span> Water Back — Fast</h2>
<p class="abs center intro" style="top:2923px">Same-Day Service Available in Palm Beach County, Florida</p>
<div class="abs map" role="img" aria-label="Map of the Palm Beach County service area with location pins"></div>
<div class="abs info" style="left:110px;top:3277px"><span class="ico-red"><svg width="11" height="11" viewBox="0 0 24 24"><path d="M6.6 10.8a15 15 0 0 0 6.6 6.6l2.2-2.2a1 1 0 0 1 1-.25 11.4 11.4 0 0 0 3.6.57 1 1 0 0 1 1 1V20a1 1 0 0 1-1 1A17 17 0 0 1 3 4a1 1 0 0 1 1-1h3.5a1 1 0 0 1 1 1c0 1.25.2 2.45.57 3.57a1 1 0 0 1-.25 1z" fill="#fff"/></svg></span>+1 555 014 2290</div>
<div class="abs info" style="left:323px;top:3277px"><span class="ico-red"><svg width="11" height="11" viewBox="0 0 24 24"><path d="M12 2a7 7 0 0 0-7 7c0 5 7 13 7 13s7-8 7-13a7 7 0 0 0-7-7zm0 9.5A2.5 2.5 0 1 1 12 6.5a2.5 2.5 0 0 1 0 5z" fill="#fff"/></svg></span>Palm Beach County, Florida</div>
<div class="abs info" style="left:110px;top:3315px"><span class="ico-red"><svg width="11" height="11" viewBox="0 0 24 24"><path d="M3 6h18v12H3z" fill="#fff"/><path d="m3 6 9 7 9-7" fill="none" stroke="#d8322a" stroke-width="2"/></svg></span>info@mrflowkettle.com</div>

<div class="abs form-card">
  <div class="field" style="top:25px"><svg width="15" height="15" viewBox="0 0 24 24"><circle cx="12" cy="8" r="4.5" fill="#777"/><path d="M3.5 21a8.5 8.5 0 0 1 17 0z" fill="#777"/></svg>Name</div>
  <div class="field" style="top:89px"><svg width="16" height="13" viewBox="0 0 24 18"><rect width="24" height="18" fill="#777"/><path d="m1 1 11 9 11-9" fill="none" stroke="#fff" stroke-width="2"/></svg>Email</div>
  <div class="field" style="top:155px"><svg width="16" height="15" viewBox="0 0 24 22"><path d="M2 22V6l6 4V6l6 4V2h8v20z" fill="#777"/></svg><span style="flex:1">Type of Service</span><svg width="12" height="8" viewBox="0 0 12 8"><path d="m1 1 5 5 5-5" fill="none" stroke="#444" stroke-width="1.6"/></svg></div>
  <div class="field" style="top:219px"><svg width="15" height="15" viewBox="0 0 24 24"><path d="M6.6 10.8a15 15 0 0 0 6.6 6.6l2.2-2.2a1 1 0 0 1 1-.25 11.4 11.4 0 0 0 3.6.57 1 1 0 0 1 1 1V20a1 1 0 0 1-1 1A17 17 0 0 1 3 4a1 1 0 0 1 1-1h3.5a1 1 0 0 1 1 1c0 1.25.2 2.45.57 3.57a1 1 0 0 1-.25 1z" fill="#777"/></svg>Phone Number</div>
  <div class="abs btn" style="left:39px;top:285px;width:136px;height:47px">Submit</div>
</div>

<h2 class="sec center" style="top:3496px"><span>What Our</span> Customers Are Saying</h2>
<div class="abs arrow-btn" style="left:41px;top:3695px"><svg width="14" height="14" viewBox="0 0 14 14"><path d="M12 7H2M6 3 2 7l4 4" fill="none" stroke="#333" stroke-width="1.6"/></svg></div>
<div class="abs arrow-btn" style="left:1132px;top:3695px"><svg width="14" height="14" viewBox="0 0 14 14"><path d="M2 7h10M8 3l4 4-4 4" fill="none" stroke="#333" stroke-width="1.6"/></svg></div>

<svg width="0" height="0" style="position:absolute"><defs><path id="star" d="M9 1l2.3 5 5.4.5-4.1 3.6 1.2 5.3L9 12.7l-4.8 2.7 1.2-5.3L1.3 6.5l5.4-.5z" fill="#f2a01e"/></defs></svg>

<div class="abs t-card" style="left:110px;top:3571px">
  <div class="stars"><svg width="18" height="17"><use href="#star"/></svg><svg width="18" height="17"><use href="#star"/></svg><svg width="18" height="17"><use href="#star"/></svg><svg width="18" height="17"><use href="#star"/></svg><svg width="18" height="17"><use href="#star"/></svg></div>
  <p class="quote">They explained my options clearly and didn’t try to upsell me. The installation was neat and done right.</p>
  <span class="more">Read More</span>
  <div class="avatar" role="img" aria-label="Customer portrait" style="background:radial-gradient(circle at 50% 40%,#c98a5e,#5a3424)"></div>
  <div class="who"><b>Dana Whitfield</b><small>Palm Beach Gardens</small></div>
</div>
<div class="abs t-card" style="left:443px;top:3571px">
  <div class="stars"><svg width="18" height="17"><use href="#star"/></svg><svg width="18" height="17"><use href="#star"/></svg><svg width="18" height="17"><use href="#star"/></svg><svg width="18" height="17"><use href="#star"/></svg><svg width="18" height="17"><use href="#star"/></svg></div>
  <p class="quote">I called three companies and Mr. FlowKettle had the best price by far. Same-day replacement and</p>
  <span class="more">Read More</span>
  <div class="avatar" role="img" aria-label="Customer portrait" style="background:radial-gradient(circle at 50% 40%,#e9e4dc,#8b6e58)"></div>
  <div class="who"><b>Dr. Arjun Mehra</b><small>Boynton Beach</small></div>
</div>
<div class="abs t-card" style="left:777px;top:3571px">
  <div class="stars"><svg width="18" height="17"><use href="#star"/></svg><svg width="18" height="17"><use href="#star"/></svg><svg width="18" height="17"><use href="#star"/></svg><svg width="18" height="17"><use href="#star"/></svg><svg width="18" height="17"><use href="#star"/></svg></div>
  <p class="quote">You can tell these guys know water heaters inside and out. No guessing, no delays—just solid work and real</p>
  <span class="more">Read More</span>
  <div class="avatar" role="img" aria-label="Customer portrait" style="background:radial-gradient(circle at 50% 40%,#f3c9a0,#e07a2e)"></div>
  <div class="who"><b>Nora Castell</b><small>Lake Worth</small></div>
</div>

<footer class="abs footer">
  <div class="abs brand" style="left:110px;top:104px;color:#fff"><span class="dot"></span>Mr. FlowKettle</div>
  <div class="abs" style="left:110px;top:284px;display:flex;gap:10px"><span class="social"></span><span class="social"></span><span class="social"></span></div>

  <p class="abs f-title" style="left:389px;top:80px">Quick Links</p>
  <ul class="abs f-list" style="left:393px;top:116px">
    <li>Home</li><li>Gas Water Heaters</li><li>Electric Water Heaters</li><li>Tankless Water Heaters</li><li>About Us</li><li>Contact Us</li>
  </ul>
  <p class="abs f-title" style="left:612px;top:80px">Services</p>
  <ul class="abs f-list" style="left:615px;top:116px">
    <li>Gas Water Heaters</li><li>Electric Water Heaters</li><li>Tankless Water Heaters</li><li>Water Heater Installation</li><li>Water Heater Repair</li><li>Water Heater Replacement</li>
  </ul>
  <p class="abs f-title" style="left:858px;top:80px">Contact Us</p>
  <div class="abs f-contact" style="left:856px;top:122px"><span class="ico-w"><svg width="10" height="10" viewBox="0 0 24 24"><path d="M6.6 10.8a15 15 0 0 0 6.6 6.6l2.2-2.2a1 1 0 0 1 1-.25 11.4 11.4 0 0 0 3.6.57 1 1 0 0 1 1 1V20a1 1 0 0 1-1 1A17 17 0 0 1 3 4a1 1 0 0 1 1-1h3.5a1 1 0 0 1 1 1c0 1.25.2 2.45.57 3.57a1 1 0 0 1-.25 1z" fill="#19236a"/></svg></span>+1 555 014 2290</div>
  <div class="abs f-contact" style="left:856px;top:172px"><span class="ico-w"><svg width="10" height="8" viewBox="0 0 24 18"><rect width="24" height="18" fill="#19236a"/></svg></span>hello@flowkettlehome.com</div>
  <div class="abs f-contact" style="left:856px;top:224px"><span class="ico-w"><svg width="10" height="10" viewBox="0 0 24 24"><path d="M12 2a7 7 0 0 0-7 7c0 5 7 13 7 13s7-8 7-13a7 7 0 0 0-7-7z" fill="#19236a"/></svg></span><span>Harbor Plaza, 210 Seabreeze Ave,<br>Jupiter, FL 33458,</span></div>
</footer>
<div class="abs news">Enter email address<span class="news-go"><svg width="18" height="18" viewBox="0 0 24 24"><path d="M22 2 2 10l8 3 3 9z" fill="#d8322a"/></svg></span></div>
<div class="abs rule"></div>
<p class="abs legal" style="left:110px;top:4298px">Privacy Policy | Terms &amp; Conditions</p>
<p class="abs legal" style="left:777px;top:4298px">© 2026 Mr. FlowKettle. All Rights Reserved.</p>

</body>
</html>
```